Animal Eye Clinic needs a Business card

We are a new veterinary ophthalmology practice (Ridgeline Pet Vision Care) and we need a business card designed. We only see animal eyes - we are not a regular veterinary clinic. We already have a logo. We are looking for a professional, good looking business card to hand out to our clients. We are looking for something simple but professional and contemporary. Our logo is likely the only picture/graphic that needs to be on the card.
Updates

Contact Information for Business Card

Delia Vossman, BSc, DVM, MSc, DipACVO
Veterinary Ophthalmologist

Phone: 250.418.3927
Email: ridgelinepetvisioncare@mailbox-example.net
Website: ridgelinepetvisioncare-example.net
Address: 1874 Thornbury Rd
Kelowna, BC, V1X 4M9

Colors

Designer to choose colors to be used in the design.

Requirements
Must have
• Our logo (attached)

```html
<!DOCTYPE html>
<html lang="en">
<head>
<meta charset="utf-8">
<title>Ridgeline Pet Vision Care – Business Card</title>
<link rel="stylesheet" href="https://fonts.googleapis.com/css2?family=Arimo:wght@400;700&display=swap">
<style>
  :root {
    --teal: #14aab4;
    --teal-deep: #0b8f9a;
    --teal-light: #2cc3cc;
    --paper: #f4f5f5;
    --paper-shade: #e3e6e7;
    --stage: #e9ecec;
    --ink-white: #ffffff;
  }
  * { box-sizing: border-box; margin: 0; padding: 0; }
  html, body { width: 1200px; height: 780px; overflow: hidden; }
  body {
    background: var(--stage);
    font-family: "Arimo", Arial, sans-serif;
    display: flex;
    align-items: center;
    justify-content: center;
    gap: 80px;
  }
  .card {
    position: relative;
    width: 340px;
    height: 595px;
    border-radius: 22px;
    overflow: hidden;
    box-shadow: 0 10px 28px rgba(0,0,0,0.18);
  }
  .card-shapes { position: absolute; inset: 0; width: 100%; height: 100%; }

  .brand {
    position: absolute;
    left: 0; right: 0;
    display: flex;
    align-items: center;
    justify-content: center;
    gap: 10px;
    color: var(--teal);
    font-weight: 700;
    font-size: 19px;
    letter-spacing: 0.02em;
    text-transform: uppercase;
    text-align: center;
    line-height: 1.15;
  }
  .brand-dot {
    flex: none;
    width: 30px; height: 30px;
    border-radius: 50%;
    background: var(--teal);
  }
  .front .brand { top: 110px; }
  .back .brand { top: 270px; flex-direction: column; gap: 14px; }
  .back .brand-dot { width: 44px; height: 44px; }

  .contact {
    position: absolute;
    top: 340px;
    left: 0; right: 0;
    text-align: center;
    color: var(--ink-white);
    font-size: 13.5px;
    line-height: 1.35;
  }
  .contact-name { font-size: 22px; font-weight: 700; margin-bottom: 2px; }
  .contact-credentials { font-size: 16px; }
  .contact-title { font-size: 13.5px; }
  .contact-rule {
    width: 210px; height: 1px; margin: 9px auto;
    background: rgba(255,255,255,0.85);
  }
  .contact-label { font-weight: 700; font-style: italic; }
  .contact-email { font-size: 12.5px; }

  .website {
    position: absolute;
    bottom: 26px; left: 0; right: 0;
    text-align: center;
    color: var(--teal);
    font-weight: 700;
    font-size: 12.5px;
    letter-spacing: 0.08em;
  }
</style>
</head>
<body>

  <section class="card front" aria-label="Business card front">
    <svg class="card-shapes" viewBox="0 0 340 595" preserveAspectRatio="none" aria-hidden="true">
      <defs>
        <linearGradient id="front-teal" x1="0" y1="0" x2="1" y2="1">
          <stop offset="0" stop-color="var(--teal-deep)"/>
          <stop offset="0.5" stop-color="var(--teal-light)"/>
          <stop offset="1" stop-color="var(--teal-deep)"/>
        </linearGradient>
      </defs>
      <rect width="340" height="595" fill="url(#front-teal)"/>
      <path d="M0 0 H340 V120 C330 220 250 290 170 318 C90 290 10 220 0 120 Z" fill="var(--paper)"/>
      <path d="M0 545 C100 522 240 522 340 548 V595 H0 Z" fill="var(--paper)"/>
    </svg>

    <div class="brand">
      <span class="brand-dot"></span>
      <span>Ridgeline Pet<br>Vision Care</span>
    </div>

    <div class="contact">
      <p class="contact-name">Delia Vossman</p>
      <p class="contact-credentials">BSc, DVM, MSc, DipACVO</p>
      <p class="contact-title">Veterinary Ophthalmologist</p>
      <div class="contact-rule"></div>
      <p>1874 Thornbury Rd</p>
      <p>Kelowna, BC, V1X 4M9</p>
      <div class="contact-rule"></div>
      <p><span class="contact-label">P:</span> 250.418.3927</p>
      <p class="contact-email"><span class="contact-label">E:</span> ridgelinepetvisioncare@mailbox-example.net</p>
    </div>

    <p class="website">ridgelinepetvisioncare-example.net</p>
  </section>

  <section class="card back" aria-label="Business card back">
    <svg class="card-shapes" viewBox="0 0 340 595" preserveAspectRatio="none" aria-hidden="true">
      <defs>
        <linearGradient id="back-teal" x1="0" y1="0" x2="1" y2="1">
          <stop offset="0" stop-color="var(--teal-light)"/>
          <stop offset="1" stop-color="var(--teal-deep)"/>
        </linearGradient>
      </defs>
      <rect width="340" height="595" fill="url(#back-teal)"/>
      <path d="M170 18 C360 150 360 445 170 577 C-20 445 -20 150 170 18 Z" fill="rgba(255,255,255,0.22)"/>
      <path d="M170 48 C330 170 330 425 170 547 C10 425 10 170 170 48 Z" fill="var(--paper)"/>
    </svg>

    <div class="brand">
      <span class="brand-dot"></span>
      <span>Ridgeline Pet<br>Vision Care</span>
    </div>
  </section>

</body>
</html>
```